I am a general contractor in Portland, Or. I would like a clean and simple design layout, maybe using the "didot" font, blue and dark bronze in colors are preferred. On one side of the card, it would be nice to have a logo(attached photo) and business name(KTW Construction). I don't need my job title on the card, just some thing along the lines of "gordon pike, general contractor". Thanks much.

Target Market(s)

Adults from 30-55 years old. Middle to upper class.

Industry/Entity Type

Contractor

Contact Information for Business Card

KTW Construction
Gordon L. Pike
2843 NE 71st Ave.
Portland, Or. 97288
541.555.0187

Font styles to use
Other font styles liked:
• didot

Colors
3277b5
7f7f7f

Requirements
Should not have
• Too much going on.

```html
<!DOCTYPE html>
<html lang="en">
<head>
<meta charset="utf-8">
<title>KTW Construction – Business Card</title>
<link rel="stylesheet" href="https://fonts.googleapis.com/css2?family=Exo+2:wght@400;500&display=swap">
<style>
  :root {
    --blue: #1e9fd6;
    --bronze: #6e5434;
    --ink: #2b2b2b;
    --grey: #555555;
    --band: #1f1f1f;
    --paper: #fbfbfb;
    --paper-shade: #e9e9e9;
    --backdrop: #d9d9d9;
  }
  * { box-sizing: border-box; margin: 0; padding: 0; }
  html, body { width: 1200px; height: 903px; overflow: hidden; }
  body {
    background: var(--backdrop);
    font-family: "Exo 2", sans-serif;
    position: relative;
  }
  .card {
    position: absolute;
    left: 250px;
    width: 700px;
    height: 400px;
    background: linear-gradient(135deg, var(--paper) 0%, var(--paper) 45%, var(--paper-shade) 100%);
    box-shadow: 0 6px 18px rgba(0,0,0,.25);
    overflow: hidden;
  }
  .card--back { top: 40px; }
  .card--front { top: 463px; }

  /* back */
  .social-band {
    position: absolute;
    left: 0; right: 0;
    top: 150px;
    height: 92px;
    background: var(--band);
    display: flex;
    align-items: center;
    justify-content: flex-end;
    padding-right: 40px;
    gap: 16px;
    color: #fff;
  }
  .social-band__label { font-size: 22px; letter-spacing: .5px; margin-right: 6px; }
  .social-band__name { font-size: 13px; font-weight: 500; }

  /* front */
  .holder { position: absolute; left: 64px; top: 42px; }
  .holder__name { color: var(--blue); font-size: 34px; font-weight: 400; letter-spacing: 1px; line-height: 1; }
  .holder__role { color: var(--bronze); font-size: 17px; font-weight: 500; letter-spacing: 1px; margin-top: 8px; }

  .contact { position: absolute; left: 0; top: 0; width: 100%; height: 100%; }
  .contact__row { position: absolute; display: flex; gap: 18px; align-items: flex-start; }
  .contact__icon { width: 22px; height: 22px; flex: none; margin-top: 2px; }
  .contact__text { color: var(--ink); font-size: 16px; letter-spacing: 1px; line-height: 27px; }
  .contact__rule { position: absolute; height: 2px; background: var(--bronze); }

  .brand {
    position: absolute;
    left: 440px; top: 180px;
    display: flex; align-items: center; gap: 12px;
  }
  .brand__dot { width: 22px; height: 22px; border-radius: 50%; background: var(--bronze); }
  .brand__name { color: var(--blue); font-size: 26px; font-weight: 500; }
</style>
</head>
<body>

<section class="card card--back" aria-label="Card back">
  <div class="social-band">
    <span class="social-band__label">follow us on here:</span>
    <span class="social-band__name">Chatter</span>
    <span class="social-band__name">Circle</span>
    <span class="social-band__name">Blogroll</span>
    <span class="social-band__name">Vidcast</span>
  </div>
</section>

<section class="card card--front" aria-label="Card front">
  <header class="holder">
    <h1 class="holder__name">GORDON PIKE</h1>
    <p class="holder__role">GENERAL CONTRACTOR</p>
  </header>

  <div class="contact">
    <div class="contact__row" style="left:62px; top:118px;">
      <svg class="contact__icon" viewBox="0 0 24 24" aria-hidden="true">
        <path fill="var(--blue)" d="M6.6 2.5l3 3.4-1.8 2.3c1.2 2.8 3.3 5 6 6.3l2.3-1.8 3.4 3-1.6 3.3C10.8 18.5 5.5 13.2 3.3 4.1z"/>
      </svg>
      <p class="contact__text">541 555 0187<br>541 555 0142</p>
    </div>
    <div class="contact__rule" style="left:55px; top:186px; width:345px;"></div>

    <div class="contact__row" style="left:62px; top:205px;">
      <svg class="contact__icon" viewBox="0 0 24 24" aria-hidden="true">
        <path fill="var(--blue)" d="M12 1.5a7 7 0 0 0-7 7c0 5.2 7 14 7 14s7-8.8 7-14a7 7 0 0 0-7-7zm0 9.8a2.8 2.8 0 1 1 0-5.6 2.8 2.8 0 0 1 0 5.6z"/>
      </svg>
      <p class="contact__text">2843 NE 71st Ave. Portland, Or. 97288</p>
    </div>
    <div class="contact__rule" style="left:45px; top:248px; width:360px;"></div>

    <div class="contact__row" style="left:62px; top:268px;">
      <svg class="contact__icon" viewBox="0 0 24 24" aria-hidden="true">
        <rect x="2" y="3" width="20" height="13" rx="1" fill="none" stroke="var(--blue)" stroke-width="2"/>
        <path d="M8 21h8M12 16v5" stroke="var(--blue)" stroke-width="2"/>
      </svg>
      <p class="contact__text">gordon@ktwbuild.com<br>www.ktwbuild.com</p>
    </div>
    <div class="contact__rule" style="left:35px; top:336px; width:350px;"></div>
  </div>

  <div class="brand">
    <span class="brand__dot" aria-hidden="true"></span>
    <span class="brand__name">KTW Construction</span>
  </div>
</section>

</body>
</html>
```